KRWB new business card design

We need a business card design for our established business which is Australia wide however based in Melbourne. We are a young team of Financial Planners who specialize in Insurance and Basic super advice for people like us.

We are people who help our clients get things done in a timely and cost effective manner whilst having a good time and a laugh along the way.

We would like this to have a consistent feel with our new e-brochure which i have attached from a color and font perspective.

Industry/Entity Type

Business

Requirements
Must have
• We do not need specific address details rather just the states we are in:

VIC/NSW/QLD/TAS
Nice to have
• Curved edge to mate the brochure

```html
<!DOCTYPE html>
<html lang="en">
<head>
<meta charset="utf-8">
<title>KRWB business card design</title>
<link rel="stylesheet" href="https://fonts.googleapis.com/css2?family=Arimo:ital,wght@0,400;0,700;1,700&family=PT+Sans&display=swap">
<style>
  :root {
    --stage: #e8e3dc;
    --label: #2a2a2a;
    --card: #ffffff;
    --ink: #111111;
    --text: #3a3a3a;
    --muted: #6f6f6f;
    --leaf: #6abf4b;
    --leaf-deep: #1f9a4a;
    --rule: #9a9a9a;
    --night-top: #2a2a2a;
    --night-bottom: #141414;
    --lime: #7cc242;
  }
  * { box-sizing: border-box; margin: 0; padding: 0; }
  html, body { width: 1200px; height: 788px; overflow: hidden; }
  body {
    position: relative;
    background: var(--stage);
    font-family: "Arimo", Arial, sans-serif;
    color: var(--text);
  }
  .view-label {
    position: absolute;
    width: 526px;
    text-align: center;
    font-family: "PT Sans", sans-serif;
    font-size: 22px;
    color: var(--label);
  }
  .card {
    position: absolute;
    width: 526px;
    height: 300px;
    border-radius: 22px;
    background: var(--card);
    overflow: hidden;
    box-shadow: 0 2px 6px rgba(0,0,0,.25);
  }
  .card > * { position: absolute; }

  /* Front */
  .brand-name {
    font-weight: 700;
    color: var(--ink);
    letter-spacing: 1px;
    line-height: 1;
  }
  .brand-mark { background: var(--leaf); }
  .front .brand-name { left: 48px; top: 20px; font-size: 46px; }
  .front .brand-mark { left: 190px; top: 30px; width: 28px; height: 28px; }
  .holder-name { left: 43px; top: 104px; font-size: 17px; font-weight: 700; color: var(--leaf); }
  .holder-role { left: 43px; top: 125px; font-size: 12.5px; font-weight: 700; color: var(--leaf-deep); }
  .rule-h { left: 35px; top: 144px; width: 278px; height: 1px; background: var(--rule); }
  .rule-v { left: 35px; top: 102px; width: 1px; height: 185px; background: var(--rule); }
  .contact-list { left: 26px; top: 151px; list-style: none; }
  .contact-list li {
    display: flex; align-items: center; gap: 7px;
    height: 22px; font-size: 14px; color: var(--text);
  }
  .contact-list svg { width: 10px; height: 10px; flex: none; }
  .contact-list .no-icon { padding-left: 17px; }

  /* Service lists */
  .services-title { font-style: italic; font-weight: 700; font-size: 18px; }
  .services { list-style: none; }
  .services li { font-size: 14px; font-weight: 700; height: 34px; }
  .services li::before { content: "\25AA\00a0"; }

  .back-one .brand-name { left: 60px; top: 130px; font-size: 46px; }
  .back-one .brand-mark { left: 82px; top: 70px; width: 40px; height: 40px; }
  .divider { left: 260px; top: 20px; width: 2px; height: 215px;
    background: linear-gradient(to bottom, transparent, #888 50%, transparent); }
  .back-one .services-title { left: 320px; top: 46px; color: var(--muted); }
  .back-one .services { left: 320px; top: 84px; }
  .back-one .services li { color: #6a6a6a; }
  .tagline-band {
    left: 0; bottom: 0; width: 100%; height: 38px;
    background: var(--leaf); color: #fff;
    font-size: 13.5px; font-weight: 700;
    display: flex; align-items: center; justify-content: center;
  }

  .back-two .services-title { left: 0; width: 526px; text-align: center; top: 47px; color: #444; }
  .back-two .services { left: 0; width: 526px; top: 85px; text-align: center; }
  .back-two .services li { color: #333; }
  .back-two .tagline { left: 0; width: 526px; text-align: center; top: 268px;
    font-size: 13.5px; font-weight: 700; color: #444; }

  .back-three { background: linear-gradient(160deg, var(--night-top), var(--night-bottom)); }
  .back-three .brand-name { left: 62px; top: 150px; font-size: 50px; color: #fff; }
  .back-three .brand-mark { left: 84px; top: 72px; width: 48px; height: 48px; }
  .back-three .services-title { left: 314px; top: 25px; color: #fff; }
  .back-three .services { left: 314px; top: 63px; }
  .back-three .services li { color: #fff; }
  .back-three .tagline { left: 314px; top: 254px; font-size: 14px; font-weight: 700;
    color: var(--lime); line-height: 18px; }
</style>
</head>
<body>
  <div class="view-label" style="left:53px; top:33px;">Front</div>
  <div class="view-label" style="left:621px; top:33px;">Back - 1</div>
  <div class="view-label" style="left:53px; top:403px;">Back - 2</div>
  <div class="view-label" style="left:621px; top:403px;">Back - 3</div>

  <section class="card front" style="left:53px; top:73px;">
    <div class="brand-name">KRWB</div>
    <div class="brand-mark"></div>
    <div class="holder-name">Daniel Hartley</div>
    <div class="holder-role">ADFS, BBus, LRS© - Financial Adviser</div>
    <div class="rule-h"></div>
    <div class="rule-v"></div>
    <ul class="contact-list">
      <li><svg viewBox="0 0 10 10"><path d="M2 1l2 2-1 1.5 2.5 2.5L7 6l2 2-1.5 1.5C5 9.5.5 5 .5 2.5z" fill="#1f9a4a"/></svg>1300 555 214</li>
      <li><svg viewBox="0 0 10 10"><rect x="1" y="3" width="8" height="6" fill="#1f9a4a"/><rect x="3" y="1" width="4" height="3" fill="#1f9a4a"/></svg>03 9555 0417</li>
      <li><svg viewBox="0 0 10 10"><rect x="2.5" y="0.5" width="5" height="9" rx="1" fill="#1f9a4a"/></svg>0400 555 826</li>
      <li><svg viewBox="0 0 10 10"><rect x="0.5" y="2" width="9" height="6" fill="#1f9a4a"/><path d="M1 2.5l4 3 4-3" stroke="#fff" fill="none"/></svg>daniel@krwb.com.au</li>
      <li><svg viewBox="0 0 10 10"><circle cx="5" cy="5" r="4.5" fill="#1f9a4a"/></svg>www.krwb.com.au</li>
      <li class="no-icon">VIC/NSW/QLD/TAS</li>
    </ul>
  </section>

  <section class="card back-one" style="left:621px; top:73px;">
    <div class="brand-mark"></div>
    <div class="brand-name">KRWB</div>
    <div class="divider"></div>
    <div class="services-title">Specialising in</div>
    <ul class="services">
      <li>Risk Insurance</li>
      <li>Debt Management</li>
      <li>Superannuation</li>
      <li>Wealth Creation</li>
      <li>Retirement Planning</li>
    </ul>
    <div class="tagline-band">SECURE FUTURE, ENHANCED LIFESTYLE</div>
  </section>

  <section class="card back-two" style="left:53px; top:445px;">
    <div class="services-title">Specialising in</div>
    <ul class="services">
      <li>Risk Insurance</li>
      <li>Debt Management</li>
      <li>Superannuation</li>
      <li>Wealth Creation</li>
      <li>Retirement Planning</li>
    </ul>
    <div class="tagline">SECURE FUTURE, ENHANCED LIFESTYLE</div>
  </section>

  <section class="card back-three" style="left:621px; top:445px;">
    <div class="brand-mark"></div>
    <div class="brand-name">KRWB</div>
    <div class="services-title">Specialising in</div>
    <ul class="services">
      <li>Risk Insurance</li>
      <li>Debt Management</li>
      <li>Superannuation</li>
      <li>Wealth Creation</li>
      <li>Retirement Planning</li>
    </ul>
    <div class="tagline">SECURE FUTURE<br>ENHANCED LIFESTYLE</div>
  </section>
</body>
</html>
```